Harborline Renewal Business Card Design

Professional and clean design. The design colors should flow with the logo. Two-sided card with the website on the back which is:

www.HarborlineRenewal.example.

"Specializing in Water Damage Restoration"

On the front I need the name, email, phone, and logo.

Name: Darnell Quisby
Email: Darnell@HarborlineRenewal.example
Phone: 555-318-2046 for now

I only have the Preview and Thumbnail right now but should have the source files uploaded within a day or two.

Target Market(s)

Flood victims, home owners with water damage from busted pipes etc...

Industry/Entity Type

Business

Contact Information for Business Card

Name: Darnell Quisby

Font styles to use
Serif
Sans Serif

Requirements
Must have
• Business Card Details Info

```html
<!DOCTYPE html>
<html lang="en">
<head>
<meta charset="utf-8">
<title>Harborline Renewal Business Card</title>
<link rel="stylesheet" href="https://fonts.googleapis.com/css2?family=Cinzel:wght@400;600&family=Open+Sans:wght@400&display=swap">
<style>
  :root {
    --page: #e9e6e2;
    --card: #2e2c2b;
    --card-edge: #242221;
    --brand-blue: #3b9fdc;
    --brand-light: #55bdf0;
    --ink-light: #f2f2f2;
    --ink-soft: #cfcfcf;
    --divider: #6a6866;
  }
  * { box-sizing: border-box; margin: 0; padding: 0; }
  html, body { width: 1200px; height: 1120px; overflow: hidden; }
  body {
    background: var(--page);
    position: relative;
    font-family: "Open Sans", Arial, sans-serif;
  }
  .card {
    position: absolute;
    left: 150px;
    width: 900px;
    height: 514px;
    background: var(--card);
    border: 1px solid var(--card-edge);
    box-shadow: 0 10px 28px rgba(0,0,0,0.25);
  }
  .card--back { top: 26px; }
  .card--front { top: 580px; }

  /* Back side */
  .brand-stack {
    position: absolute;
    left: 0; right: 0; top: 70px;
    display: flex; flex-direction: column; align-items: center;
  }
  .brand-dot {
    width: 200px; height: 200px; border-radius: 50%;
    background: var(--brand-light);
  }
  .brand-name--large {
    margin-top: 26px;
    font-family: "Cinzel", Georgia, serif;
    font-weight: 600;
    font-size: 40px;
    letter-spacing: 2px;
    color: var(--brand-blue);
  }
  .tagline {
    position: absolute;
    left: 0; right: 0; bottom: 56px;
    text-align: center;
    font-family: "Cinzel", Georgia, serif;
    font-size: 25px;
    letter-spacing: 1px;
    color: var(--brand-blue);
  }

  /* Front side */
  .brand-block {
    position: absolute;
    left: 40px; top: 150px;
    width: 330px;
    display: flex; flex-direction: column; align-items: center;
  }
  .brand-dot--small { width: 96px; height: 96px; }
  .brand-name {
    margin-top: 18px;
    font-family: "Cinzel", Georgia, serif;
    font-weight: 600;
    font-size: 34px;
    line-height: 1.15;
    text-align: center;
    color: var(--brand-blue);
  }
  .divider {
    position: absolute;
    left: 400px; top: 150px;
    width: 2px; height: 190px;
    background: var(--divider);
  }
  .contact-block {
    position: absolute;
    left: 440px; top: 140px;
    color: var(--ink-light);
  }
  .person-name {
    font-family: "Cinzel", Georgia, serif;
    font-weight: 600;
    font-size: 30px;
    letter-spacing: 1px;
  }
  .person-title {
    font-family: "Cinzel", Georgia, serif;
    font-size: 24px;
    color: var(--ink-soft);
    letter-spacing: 1px;
    margin-bottom: 28px;
  }
  .contact-list { list-style: none; }
  .contact-item {
    display: flex; align-items: center; gap: 12px;
    font-size: 19px;
    line-height: 30px;
    color: var(--ink-light);
  }
  .contact-icon { width: 18px; height: 18px; flex: none; }
</style>
</head>
<body>

  <section class="card card--back" aria-label="Card back">
    <div class="brand-stack">
      <div class="brand-dot"></div>
      <div class="brand-name--large">Harborline Renewal</div>
    </div>
    <p class="tagline">Specializing in Water Damage Restoration</p>
  </section>

  <section class="card card--front" aria-label="Card front">
    <div class="brand-block">
      <div class="brand-dot brand-dot--small"></div>
      <div class="brand-name">Harborline<br>Renewal</div>
    </div>

    <div class="divider"></div>

    <div class="contact-block">
      <h1 class="person-name">Darnell Quisby</h1>
      <p class="person-title">Title</p>
      <ul class="contact-list">
        <li class="contact-item">
          <svg class="contact-icon" viewBox="0 0 24 24" aria-hidden="true"><path fill="#f2f2f2" d="M6.6 10.8a15 15 0 0 0 6.6 6.6l2.2-2.2a1 1 0 0 1 1-.25 11.4 11.4 0 0 0 3.6.57 1 1 0 0 1 1 1V20a1 1 0 0 1-1 1A17 17 0 0 1 3 4a1 1 0 0 1 1-1h3.5a1 1 0 0 1 1 1c0 1.25.2 2.45.57 3.57a1 1 0 0 1-.25 1z"/></svg>
          <span>555-318-2046</span>
        </li>
        <li class="contact-item">
          <svg class="contact-icon" viewBox="0 0 24 24" aria-hidden="true"><rect x="2" y="5" width="20" height="14" rx="2" fill="#f2f2f2"/><path d="M3 6l9 7 9-7" fill="none" stroke="#2e2c2b" stroke-width="1.8"/></svg>
          <span>Darnell@HarborlineRenewal.example</span>
        </li>
        <li class="contact-item">
          <svg class="contact-icon" viewBox="0 0 24 24" aria-hidden="true"><g fill="none" stroke="#f2f2f2" stroke-width="1.8"><circle cx="12" cy="12" r="9.5"/><ellipse cx="12" cy="12" rx="4" ry="9.5"/><path d="M2.5 12h19M4 7h16M4 17h16"/></g></svg>
          <span>www.HarborlineRenewal.example</span>
        </li>
      </ul>
    </div>
  </section>

</body>
</html>
```